Website for Vornelix Capital, my new firm that raises money from investors to buy, build, own an...

Vornelix Capital needs a website! We are a new company with very experienced people, who invest in, own and build hotel properties, as well as apartments and other commercial real estate. We seek investors for our projects, and we provide safe, secure returns on their investment in our projects. Our new logo is designed to exhibit strength, class and security, and would like our website to continue on this theme. Our name, Vornelix, is a word-play on a Greek word “aristeia”, which means “excellence” and “a warriors finest moment of glory in war”. If you are in business, you realize that much of it is like war, with strategy and moves and opponents and competitors, and ever-changing economic conditions and threats that make business very much like war. We like to think that we are good at business (war), and so have named our company “Vornelix”, using the founders last name and the word “aristeia” combined. Another definition of "aristeia" is "performing at the peak of one's potential after a long struggle"...again, much like business in real life! The website design should exhibit financial security, smart moves, and positive growth towards a bright future.

Target Market(s)

The target market is smart and wealthy investors, with others such as brokers, cities and government agencies, lenders, sellers, partners, etc also looking at it.

Industry/Entity Type

Investment

Number of Pages Required

5+ page

Font styles to use
Sans Serif

Colors
fec214

Requirements
Must have
• Our website should have a landing page, a "about" or bio page, a projects page and a contact us page. Our new logo uses the colors black and gold, so this should be factored in to our site. The site should be simple, yet impactful and impressive. I have actually two logos, which can be mixed and interchanged in a complimentary way, each with their own unique look.
Nice to have
• I have uploaded a couple screenshots of a website i like, and the simplicity I mention.
Should not have
• The site should not be flashy or complicated or complex or "busy"

```html
<!DOCTYPE html>
<html lang="en">
<head>
<meta charset="utf-8">
<title>Vornelix Capital</title>
<link href="https://fonts.googleapis.com/css2?family=Lato:wght@400;700;900&display=swap" rel="stylesheet">
<style>
  :root {
    --gold: #fec214;
    --gold-dark: #d99f00;
    --ink: #111111;
    --text: #333333;
    --muted-bg: #f1f1f1;
    --white: #ffffff;
    --dark: #2f2f2f;
    --field: #ececec;
  }
  * { margin: 0; padding: 0; box-sizing: border-box; }
  html, body { width: 1200px; height: 2812px; overflow: hidden; }
  body { font-family: 'Lato', sans-serif; color: var(--text); background: var(--white); position: relative; }
  section, header, footer { position: absolute; left: 0; width: 1200px; }
  .abs { position: absolute; }
  .center { left: 0; width: 1200px; text-align: center; }

  /* header */
  .site-header { top: 0; height: 79px; background: var(--white); z-index: 3; }
  .brand-badge { left: 62px; top: -10px; width: 150px; height: 150px; border-radius: 50%; background: var(--white);
    display: flex; align-items: center; justify-content: center; z-index: 4; }
  .brand-name { font-weight: 900; font-size: 23px; color: var(--ink); letter-spacing: 1px; }
  .main-nav { right: 72px; top: 32px; display: flex; gap: 32px; font-size: 13px; font-weight: 700; }
  .main-nav a { color: var(--ink); text-decoration: none; }
  .main-nav a.active { color: var(--gold); }

  /* hero */
  .hero { top: 79px; height: 545px; }
  .hero-photo { left: 0; top: 0; width: 1200px; height: 545px;
    background: linear-gradient(100deg, #2a2b2e 0%, #5d5f63 30%, #8a8c8f 55%, #4b4c50 80%, #222326 100%); }
  .hero-title { top: 175px; font-size: 74px; font-weight: 700; color: var(--white); letter-spacing: 2px; }
  .hero-sub { top: 263px; font-size: 22px; font-weight: 700; color: var(--white); line-height: 30px; }
  .btn { display: inline-block; background: var(--gold); color: var(--white); font-size: 15px; font-weight: 700;
    text-transform: uppercase; border-bottom: 4px solid var(--gold-dark); text-align: center; }
  .hero .btn { left: 510px; top: 341px; width: 180px; height: 47px; line-height: 45px; }
  .dots { display: flex; justify-content: center; gap: 8px; }
  .dots span { width: 13px; height: 13px; border-radius: 50%; background: var(--white); }
  .dots span.on { background: var(--gold); }
  .hero .dots { top: 484px; }

  h2 { font-size: 32px; font-weight: 900; color: var(--ink); }
  .lead { font-size: 15px; line-height: 35px; color: var(--text); }

  /* welcome */
  .welcome { top: 624px; height: 413px; }
  .welcome h2 { top: 56px; }
  .welcome .lead { left: 150px; width: 900px; top: 106px; text-align: center; }
  .welcome .btn { left: 510px; top: 282px; width: 180px; height: 48px; line-height: 46px; }

  /* services */
  .services { top: 1037px; height: 538px; background: var(--muted-bg); }
  .services h2 { top: 53px; }
  .services .lead { top: 102px; }
  .cards { left: 75px; top: 171px; display: flex; gap: 28px; }
  .card { position: relative; width: 242px; height: 283px; background: var(--white); border-radius: 12px; text-align: center; }
  .card::after { content: ""; position: absolute; left: 30px; right: 30px; bottom: -22px; height: 22px; border-radius: 50%;
    background: radial-gradient(ellipse at center, rgba(0,0,0,.45), rgba(0,0,0,0) 70%); }
  .card svg { margin-top: 38px; height: 64px; }
  .card h3 { margin-top: 18px; font-size: 22px; font-weight: 700; color: var(--gold); }
  .card p { margin: 10px auto 0; width: 200px; font-size: 15px; line-height: 25px; color: var(--ink); }

  /* projects */
  .projects { top: 1575px; height: 544px; }
  .projects h2 { top: 50px; }
  .projects .lead { top: 99px; }
  .project-grid { left: 75px; top: 167px; display: flex; gap: 30px; }
  .project { width: 330px; text-align: center; }
  .project-photo { width: 330px; height: 198px; }
  .project h3 { margin-top: 28px; font-size: 18px; font-weight: 400; color: var(--gold); line-height: 26px; text-transform: uppercase; }
  .project a { display: block; margin-top: 15px; font-size: 15px; font-weight: 700; color: var(--ink); text-decoration: none; }

  /* testimonials */
  .testimonials { top: 2119px; height: 435px;
    background: linear-gradient(120deg, #2b2b2b 0%, #3d3d3d 40%, #2e2e2e 70%, #393939 100%); }
  .testimonials h2 { top: 60px; color: var(--white); }
  .quote-mark { left: 576px; top: 136px; }
  .testimonials .lead { left: 150px; width: 900px; top: 185px; text-align: center; color: var(--white); line-height: 28px; }
  .quote-name { top: 284px; font-size: 16px; font-weight: 700; color: var(--gold); }
  .testimonials .dots { top: 371px; }

  /* footer */
  .site-footer { top: 2554px; height: 258px; background: var(--white); }
  .footer-brand { left: 75px; top: 72px; display: flex; align-items: center; gap: 8px; }
  .footer-brand .dot { width: 14px; height: 14px; background: var(--gold); border-radius: 50%; }
  .footer-brand .brand-name { font-size: 19px; }
  .copyright { left: 78px; top: 138px; font-size: 12px; line-height: 23px; color: var(--ink); }
  .social { left: 78px; top: 194px; display: flex; gap: 17px; }
  .social span { width: 20px; height: 20px; border-radius: 50%; background: var(--ink); }
  .footer-col h4 { font-size: 14px; font-weight: 700; color: var(--ink); margin-bottom: 14px; }
  .footer-col li { list-style: none; font-size: 12px; line-height: 27.6px; color: var(--ink); }
  .col-links { left: 388px; top: 47px; }
  .col-projects { left: 632px; top: 47px; }
  .col-signup { left: 887px; top: 47px; }
  .field { width: 234px; height: 34px; background: var(--field); font-size: 11px; color: var(--ink); padding-left: 12px; line-height: 34px; margin-bottom: 11px; }
  .signup-btn { left: 1027px; top: 174px; width: 94px; height: 32px; line-height: 32px; background: var(--gold); color: var(--white);
    font-size: 12px; font-weight: 700; text-align: center; }
</style>
</head>
<body>

<header class="site-header">
  <div class="abs brand-badge"><span class="brand-name">VORNELIX</span></div>
  <nav class="abs main-nav">
    <a class="active" href="#">HOME</a>
    <a href="#">ABOUT US</a>
    <a href="#">PROJECTS</a>
    <a href="#">CONTACT US</a>
  </nav>
</header>

<section class="hero">
  <div class="abs hero-photo" role="img" aria-label="Business people in suits shaking hands over architectural models of apartment buildings"></div>
  <h1 class="abs center hero-title">VORNELIX CAPITAL</h1>
  <p class="abs center hero-sub">Lanventore veritatis et quasi architecto beatae<br>vitae dicta sunt explicabo.</p>
  <a class="abs btn" href="#">Read More</a>
  <div class="abs center dots"><span class="on"></span><span></span><span></span><span></span></div>
</section>

<section class="welcome">
  <h2 class="abs center">Welcome to Our Website</h2>
  <p class="abs lead">Lorem ipsum dolor sit amet, consectetur adipisicing elit, sed do eiusmod tempor incididunt ut labore et doloreasdes magna aliqua. Ut enim ad minim veniam, quis nostrud exercitation ullamco laboris nisi ut aliquip ex ea commodalo consequat. Duis aute irure dolor in reprehenderit in voluptate velit esse cillum dolore eu fugiat nulla pariatur. Excepteur sint occaecat cupidatat non proident, sunt in culpa qui officia deserunt mollit anim id est laborum</p>
  <a class="abs btn" href="#">Read More</a>
</section>

<section class="services">
  <h2 class="abs center">What We Do</h2>
  <p class="abs center lead">Lorem ipsum dolor sit amet, consectetur adipisicing elit, sed do eiusmod tempor incididunt ut labore et doloreasdes magna aliqua.</p>
  <div class="abs cards">
    <div class="card">
      <svg viewBox="0 0 40 64" width="40" aria-hidden="true"><text x="20" y="56" text-anchor="middle" font-family="Lato, sans-serif" font-weight="900" font-size="64" fill="#333">$</text></svg>
      <h3>Elementum</h3>
      <p>Lorem ipsum dolor sit amet, consectetur adipisicing elit, sed do eiusmod tempor incididunt..</p>
    </div>
    <div class="card">
      <svg viewBox="0 0 48 64" width="48" aria-hidden="true"><rect x="0" y="0" width="48" height="64" rx="2" fill="#333"/>
        <g fill="#fff"><rect x="8" y="8" width="6" height="6"/><rect x="21" y="8" width="6" height="6"/><rect x="34" y="8" width="6" height="6"/>
        <rect x="8" y="20" width="6" height="6"/><rect x="21" y="20" width="6" height="6"/><rect x="34" y="20" width="6" height="6"/>
        <rect x="8" y="32" width="6" height="6"/><rect x="21" y="32" width="6" height="6"/><rect x="34" y="32" width="6" height="6"/>
        <rect x="18" y="48" width="12" height="16"/></g></svg>
      <h3>Pellentesque</h3>
      <p>Lorem ipsum dolor sit amet, consectetur adipisicing elit, sed do eiusmod tempor incididunt..</p>
    </div>
    <div class="card">
      <svg viewBox="0 0 72 52" width="72" style="margin-top:50px;height:52px" aria-hidden="true"><g fill="#333">
        <rect x="0" y="0" width="5" height="52"/><rect x="0" y="47" width="72" height="5"/>
        <rect x="14" y="24" width="9" height="20"/><rect x="28" y="30" width="9" height="14"/><rect x="42" y="16" width="9" height="28"/><rect x="56" y="8" width="9" height="36"/></g></svg>
      <h3>Pellentesque</h3>
      <p>Lorem ipsum dolor sit amet, consectetur adipisicing elit, sed do eiusmod tempor incididunt..</p>
    </div>
    <div class="card">
      <svg viewBox="0 0 50 64" width="50" aria-hidden="true"><path d="M0 0 H34 L50 16 V64 H0 Z" fill="#333"/>
        <g fill="#fff"><rect x="10" y="26" width="30" height="4"/><rect x="10" y="36" width="30" height="4"/><rect x="10" y="46" width="30" height="4"/></g></svg>
      <h3>Pellentesque</h3>
      <p>Lorem ipsum dolor sit amet, consectetur adipisicing elit, sed do eiusmod tempor incididunt..</p>
    </div>
  </div>
</section>

<section class="projects">
  <h2 class="abs center">Our Projects</h2>
  <p class="abs center lead">Lorem ipsum dolor sit amet, consectetur adipisicing elit, sed do eiusmod tempor incididunt ut labore et doloreasdes magna aliqua.</p>
  <div class="abs project-grid">
    <div class="project">
      <div class="project-photo" role="img" aria-label="Modern glass office building among green trees under a blue sky" style="background:linear-gradient(180deg,#8fb6e0 0%,#6f8fa8 45%,#4e6a4a 100%)"></div>
      <h3>Lorem ipsum dolor sit amet,<br>consectetur</h3>
      <a href="#">READ MORE</a>
    </div>
    <div class="project">
      <div class="project-photo" role="img" aria-label="White modern apartment block with landscaped lawn" style="background:linear-gradient(180deg,#b9d3ea 0%,#d9dcd8 45%,#5f8a48 100%)"></div>
      <h3>Lorem ipsum dolor sit amet,<br>consectetur</h3>
      <a href="#">READ MORE</a>
    </div>
    <div class="project">
      <div class="project-photo" role="img" aria-label="Large illuminated hotel building at dusk" style="background:linear-gradient(180deg,#1f3fae 0%,#3a4f9a 45%,#b08a4a 80%,#3a3328 100%)"></div>
      <h3>Lorem ipsum dolor sit amet,<br>consectetur</h3>
      <a href="#">READ MORE</a>
    </div>
  </div>
</section>

<section class="testimonials" role="img" aria-label="Dark faceted geometric background">
  <h2 class="abs center">Testimonials</h2>
  <svg class="abs quote-mark" width="48" height="38" viewBox="0 0 48 38" aria-hidden="true"><g fill="#fec214">
    <path d="M0 0 H20 V20 Q20 34 6 38 L4 32 Q11 28 11 22 H0 Z"/><path d="M26 0 H46 V20 Q46 34 32 38 L30 32 Q37 28 37 22 H26 Z"/></g></svg>
  <p class="abs lead">Lorem ipsum dolor sit amet, consectetur adipisicing elit, sed do eiusmod tempor incididunt ut labore et doloreasdes magna aliqua. Ut enim ad minim veniam, quis nostrud exercitation ullamco laboris nisi ut aliquip ex ea commodalo consequat. Duis aute irure dolor in reprehenderit in voluptate velit esse cillum dolore eu fugiat nulla pariatur.</p>
  <p class="abs center quote-name">-Name Heading</p>
  <div class="abs center dots"><span class="on"></span><span></span><span></span><span></span></div>
</section>

<footer class="site-footer">
  <div class="abs footer-brand"><span class="dot"></span><span class="brand-name">VORNELIX</span></div>
  <p class="abs copyright">Copyright © 2018, Company Name<br>All Right reserved</p>
  <div class="abs social" aria-label="Social links"><span></span><span></span><span></span><span></span><span></span></div>
  <div class="abs footer-col col-links">
    <h4>QUICK LINKS</h4>
    <ul><li>Home</li><li>About us</li><li>Projects</li><li>Contact Us</li></ul>
  </div>
  <div class="abs footer-col col-projects">
    <h4>PROJECTS</h4>
    <ul><li>Excepteur sint</li><li>Occaecat cupidatat</li><li>Proident, sunt</li><li>Culpa qui officia</li><li>Deserunt</li></ul>
  </div>
  <div class="abs footer-col col-signup">
    <h4>EMAIL SIGN UP</h4>
    <div class="field">ENTER NAME</div>
    <div class="field">ENTER EMAIL</div>
  </div>
  <div class="abs signup-btn">SIGN UP</div>
</footer>

</body>
</html>
```